Glen Whitmore Professional Coaching

I would like a website with a mountain theme geared towards professional executives reaching higher peaks and goals. This is a 3 page website with brand essence information on the opening page, the coaching process on a second page and "about me" and lead capture form on a third page

Target Market(s)

C-Level audience, involved in tech, government, manufacturing, and transportation type of corporations

Coding

Coded - Design and coding required

Number of Pages Required

3 page

Font styles to use
Sans Serif

Colors
a7a7a7
1b1b1b
e8e8e8
3176b5
abd036
0355a3

Requirements
Must have
• Looking for a user friendly site that I can manage/update going forward. Must have:
• 1. "Is coaching right for you?" - page 1
• 2. "Our Process" page 2 - I will describe how we approach coaching
• 3. "Contact us" page 3 where I can capture contact information from potential clients
• 4. Clean and professional with more modern font
• 5. Links to personal social media sites
• 6. Ability to upload/download .pdf documents as resources
• 7. Ability to add on new pages in the future (such as a blog page)
Nice to have
• I want a place to store articles I write or use.
• LinkedIn or Twitter Feed
Should not have
• Not fluffy or too 'zen' like personal life coaches tend to present.

```html
<!DOCTYPE html>
<html lang="en">
<head>
<meta charset="utf-8">
<title>Glen Whitmore Professional Coaching</title>
<link href="https://fonts.googleapis.com/css2?family=Lato:wght@400;700;900&display=swap" rel="stylesheet">
<style>
:root{
  --orange:#f5821f;
  --blue:#3a9ad9;
  --ink:#2b2b2b;
  --text:#444;
  --light:#f2f2f2;
  --white:#fff;
}
*{box-sizing:border-box;margin:0;padding:0}
html,body{width:1200px;height:3340px;overflow:hidden}
body{font-family:'Lato',sans-serif;color:var(--text);background:var(--white);position:relative}
section,header,footer{position:absolute;left:0;width:1200px}
.abs{position:absolute}
.center{text-align:center;left:0;width:1200px}

/* header */
.site-header{top:0;height:122px;background:var(--white)}
.brand{left:76px;top:28px;line-height:1}
.brand-name{font-size:38px;font-weight:900;color:var(--ink);letter-spacing:.5px}
.brand-sub{font-size:27px;font-weight:700;color:var(--blue);margin-top:4px;letter-spacing:.5px}
.nav{right:76px;top:42px;display:flex;gap:0;align-items:center}
.nav a{font-size:13px;font-weight:700;color:var(--ink);text-decoration:none;padding:0 20px;height:38px;line-height:38px;text-transform:uppercase}
.nav a.active{background:var(--orange);color:var(--white);border-radius:19px;padding:0 28px}

/* hero */
.hero{top:122px;height:573px;background:linear-gradient(180deg,#3b2a3f 0%,#7a5560 30%,#b07c6a 55%,#6b4a45 80%,#3e2d30 100%)}
.hero-title{top:195px;font-size:60px;font-weight:900;color:var(--white)}
.hero-sub{top:268px;font-size:28px;font-weight:700;color:var(--white)}
.btn-solid{left:519px;top:319px;width:164px;height:42px;border-radius:21px;background:var(--blue);color:var(--white);font-size:17px;font-weight:700;line-height:42px;text-align:center}
.dots{top:524px;display:flex;justify-content:center;gap:10px}
.dots span{width:10px;height:10px;border-radius:50%;background:var(--white)}
.dots span:first-child{background:#6cc6c0}

/* welcome */
.welcome{top:695px;height:410px}
.section-title{font-size:29px;font-weight:700;color:var(--ink);line-height:34px;text-transform:uppercase}
.welcome .section-title{top:63px}
.welcome p{top:153px;font-size:16px;line-height:27px;color:var(--text);padding:0 80px}
.btn-outline{height:46px;border:2px solid var(--orange);border-radius:23px;color:var(--orange);font-size:15px;font-weight:700;line-height:42px;text-align:center;text-transform:uppercase}
.welcome .btn-outline{left:512px;top:293px;width:178px}

/* process */
.process{top:1105px;height:628px;background:linear-gradient(135deg,#3a3633 0%,#2a2826 45%,#35302d 100%)}
.process .section-title{top:67px;color:var(--white)}
.process .lead{top:114px;font-size:16px;color:var(--white)}
.step{width:340px;text-align:center;color:var(--white)}
.step-circle{width:228px;height:228px;border-radius:50%;background:var(--orange);border:5px solid var(--white);margin:0 auto;display:flex;align-items:center;justify-content:center}
.step-num{margin-top:32px;font-size:17px;font-weight:700}
.step-name{font-size:19px;font-weight:700;color:var(--blue);margin-top:4px;text-transform:uppercase}
.step-text{font-size:14px;line-height:24px;margin-top:6px;padding:0 20px}
.arrow{top:270px}

/* about */
.about{top:1733px;height:499px}
.about-photo{left:76px;top:70px;width:385px;height:363px;border-radius:18px;background:linear-gradient(160deg,#4d6b3a 0%,#7e9a5c 40%,#3d4f63 75%,#2c3a4f 100%)}
.about-body{left:520px;width:604px;text-align:center}
.about .section-title{top:108px}
.about p{top:160px;font-size:15px;line-height:27px}
.about .btn-outline{left:213px;top:344px;width:178px}

/* blog */
.blog{top:2232px;height:472px;background:var(--light)}
.blog .section-title{top:48px}
.post{top:117px;width:329px}
.post-image{height:178px;background:linear-gradient(135deg,#9fb0bf 0%,#d9dde0 50%,#6d7b87 100%)}
.post-title{margin-top:20px;font-size:16px;font-weight:700;line-height:25px;color:var(--orange)}
.post-link{margin-top:12px;font-size:13px;font-weight:700;color:var(--blue)}

/* subscribe */
.subscribe{top:2704px;height:499px;background:linear-gradient(120deg,#4a4440 0%,#2f2b29 50%,#433b38 100%)}
.subscribe h2{left:165px;top:214px;font-size:35px;font-weight:900;line-height:42px;color:var(--white);text-transform:uppercase}
.signup{left:723px;top:93px;width:312px;height:312px;border-radius:50%;background:rgba(58,154,217,.92);text-align:center}
.signup h3{margin-top:70px;font-size:19px;font-weight:700;color:var(--white)}
.field,.signup-btn{width:222px;height:36px;border-radius:18px;margin:12px auto 0;font-size:13px;line-height:36px}
.field{background:var(--white);color:var(--ink)}
.signup-btn{background:var(--orange);color:var(--white);font-weight:700;text-transform:uppercase}
.signup h3 + .field{margin-top:15px}

/* footer */
.site-footer{top:3203px;height:137px;background:var(--white)}
.copyright{top:37px;font-size:14px;color:var(--ink)}
.social{top:73px;display:flex;justify-content:center;gap:14px}
.social span{font-size:13px;font-weight:700;color:var(--ink)}
</style>
</head>
<body>

<header class="site-header">
  <div class="brand abs">
    <div class="brand-name">GLEN WHITMORE</div>
    <div class="brand-sub">PROFESSIONAL COACHING</div>
  </div>
  <nav class="nav abs">
    <a class="active" href="#">Home</a>
    <a href="#">About Me</a>
    <a href="#">Coaching Process</a>
    <a href="#">Contact Us</a>
  </nav>
</header>

<section class="hero" role="img" aria-label="Snow-capped mountain peak at sunset">
  <h1 class="hero-title abs center">Glen Whitmore</h1>
  <div class="hero-sub abs center">Professional Coaching</div>
  <div class="btn-solid abs">Read More</div>
  <div class="dots abs center"><span></span><span></span><span></span><span></span></div>
</section>

<section class="welcome">
  <h2 class="section-title abs center">Welcome to<br>Glen Whitmore Professional Coaching</h2>
  <p class="abs center">Aliquam molestie, mi et imperdiet euismod, dui purus auctor tellus, et interdum lacus lectus et ante. Sed accumsan sollicitudin sapien,<br>sit amet adipiscing turpis gravida ac. In congue, neque ac lobortis volutpat, libero mauris varius mi, vitae suscipit ipsum ligula vitae risus.<br>Duis aliquam nibh a dui iaculis viverra id a velit. Vivamus egestas risus in magna varius commodo. Sed semper viverra egestas.<br>Etiam pretium porttitor lectus, vel ornare neque porta volutpat.</p>
  <div class="btn-outline abs">Read More</div>
</section>

<section class="process" role="img" aria-label="Coach presenting to a seated audience, darkened">
  <h2 class="section-title abs center">Coaching Process</h2>
  <div class="lead abs center">Aliquam molestie, mi et imperdiet euismod, dui purus auctor tellus, et interdum lacus lectus et ante.</div>

  <div class="step abs" style="left:70px;top:170px">
    <div class="step-circle">
      <svg width="100" height="80" viewBox="0 0 100 80" fill="none" stroke="#fff" stroke-width="7"><rect x="14" y="6" width="72" height="50" rx="4"/><path d="M4 68h92" stroke-linecap="round"/></svg>
    </div>
    <div class="step-num">STEP 1</div>
    <div class="step-name">Nunc Condimentum</div>
    <div class="step-text">Aliquam molestie, mi et imperdiet euismod, dui purus auctor tellus, et interdum lacus lectus et ante...</div>
  </div>
  <div class="step abs" style="left:429px;top:170px">
    <div class="step-circle">
      <svg width="90" height="110" viewBox="0 0 90 110"><path d="M8 4h52l26 26v76H8z" fill="#fff"/><path d="M60 4v26h26" fill="#f5821f"/><rect x="22" y="48" width="48" height="7" fill="#f5821f"/><rect x="22" y="64" width="48" height="7" fill="#f5821f"/><rect x="22" y="80" width="48" height="7" fill="#f5821f"/></svg>
    </div>
    <div class="step-num">STEP 2</div>
    <div class="step-name">Nunc Condimentum</div>
    <div class="step-text">Aliquam molestie, mi et imperdiet euismod, dui purus auctor tellus, et interdum lacus lectus et ante...</div>
  </div>
  <div class="step abs" style="left:787px;top:170px">
    <div class="step-circle">
      <svg width="120" height="100" viewBox="0 0 120 100" fill="#fff"><rect x="40" y="4" width="74" height="48" fill="none" stroke="#fff" stroke-width="5"/><path d="M50 42l16-14 12 8 24-22" fill="none" stroke="#fff" stroke-width="4"/><circle cx="22" cy="18" r="9"/><rect x="12" y="30" width="20" height="28" rx="4"/><circle cx="18" cy="70" r="7"/><rect x="8" y="80" width="20" height="16" rx="4"/><circle cx="46" cy="70" r="7"/><rect x="36" y="80" width="20" height="16" rx="4"/><circle cx="74" cy="70" r="7"/><rect x="64" y="80" width="20" height="16" rx="4"/><circle cx="102" cy="70" r="7"/><rect x="92" y="80" width="20" height="16" rx="4"/></svg>
    </div>
    <div class="step-num">STEP 3</div>
    <div class="step-name">Nunc Condimentum</div>
    <div class="step-text">Aliquam molestie, mi et imperdiet euismod, dui purus auctor tellus, et interdum lacus lectus et ante...</div>
  </div>

  <svg class="arrow abs" style="left:372px" width="100" height="70" viewBox="0 0 100 70" fill="none" stroke="#ddd" stroke-width="3"><path d="M6 10c30 0 60 20 82 48"/><path d="M70 56l18 2-2-18"/></svg>
  <svg class="arrow abs" style="left:730px" width="100" height="70" viewBox="0 0 100 70" fill="none" stroke="#ddd" stroke-width="3"><path d="M6 60c20-30 50-46 84-48"/><path d="M74 2l16 10-14 12"/></svg>
</section>

<section class="about">
  <div class="about-photo abs" role="img" aria-label="Portrait of the coach outdoors in a blazer"></div>
  <div class="about-body abs" style="top:0;height:499px">
    <h2 class="section-title abs" style="left:0;width:604px">About Me</h2>
    <p class="abs" style="left:0;width:604px">Aliquam molestie, mi et imperdiet euismod, dui purus auctor tellus, et interdum lacus<br>lectus et ante. Sed accumsan sollicitudin sapien, sit amet adipiscing turpis gravida ac.<br>In congue, neque ac lobortis volutpat, libero mauris varius mi, vitae suscipit ipsum ligula<br>vitae risus. Duis aliquam nibh a dui iaculis viverra id a velit. Vivamus egestas risus in<br>magna varius commodo. Sed semper viverra egestas.</p>
    <div class="btn-outline abs">Read More</div>
  </div>
</section>

<section class="blog">
  <h2 class="section-title abs center">Blog Posts</h2>
  <article class="post abs" style="left:76px">
    <div class="post-image" role="img" aria-label="Team meeting around a table with charts"></div>
    <div class="post-title">Lorem ipsum dolor sit amet, consectetur adipiscing elit posuere quis nisi vitae pharetra...</div>
    <div class="post-link">Read More</div>
  </article>
  <article class="post abs" style="left:435px">
    <div class="post-image" role="img" aria-label="Speaker addressing a boardroom"></div>
    <div class="post-title">Lorem ipsum dolor sit amet, consectetur adipiscing elit posuere quis nisi vitae pharetra...</div>
    <div class="post-link">Read More</div>
  </article>
  <article class="post abs" style="left:795px">
    <div class="post-image" role="img" aria-label="Presenter leading a workshop"></div>
    <div class="post-title">Lorem ipsum dolor sit amet, consectetur adipiscing elit posuere quis nisi vitae pharetra...</div>
    <div class="post-link">Read More</div>
  </article>
</section>

<section class="subscribe" role="img" aria-label="Speaker in front of a seminar audience, darkened">
  <h2 class="abs">Subscribe to my weekly<br>newsletters</h2>
  <div class="signup abs">
    <h3>EMAIL SIGN UP</h3>
    <div class="field">Enter Name</div>
    <div class="field">Email Address</div>
    <div class="signup-btn">Subscribe</div>
  </div>
</section>

<footer class="site-footer">
  <div class="copyright abs center">Copyright © 2019. Company Name. All Right Reserved</div>
  <div class="social abs center"><span>Updates</span><span>Posts</span><span>Videos</span><span>Circle</span><span>Photos</span><span>Profile</span></div>
</footer>

</body>
</html>
```